Harborview Estates Business Card for Apartment Buildings

Create business cards for resident managers who run apartment buildings. The audience is the public who are searching for apartment rentals, and current residents who live at the apartment building. Key design element will be incorporating the company logo, however, the logo cannot dominate. The building name and manager name are more important than the logo. Current business card design leaves little room for copy, so we may need to reduce the size on the current card to allow for more space for copy.

Target Market(s)

Adults 18-65 years of age, who are looking for an apartment rental, plus current residents who live at our apartment buildings.

Industry/Entity Type

Property Management

Contact Information for Business Card

A major design element will be use of the company logo. Important property and manager contact information must be part of the design. The size of the logo will need to be reduced to make room for building and manager contact copy.

Font styles to use
Sans Serif

Colors
3176b5
000000
959595
ffffff

Requirements
Must have
• 1) Incorporate the company logo.
• 2) Use the company colors (dark blue, black/grey, over white).
• 3) FEATURE THE BUILDING NAME
• 4) FEATURE THE MANAGER NAME
• 5) The company name is less important than BUILDING and MANAGER
• 6) Manager contact information
• **SEE ATTACHED CREATIVE BRIEF**
Nice to have
• 1) Back of card logo watermark
• 2) Ability to write notes on back of carfd
Should not have
• Avoid letting the company logo dominate the card, the building name and manager are more important than the company logo.

```html
<!DOCTYPE html>
<html lang="en">
<head>
<meta charset="utf-8">
<title>Harborview Estates — Business Card</title>
<link href="https://fonts.googleapis.com/css2?family=Roboto:wght@400;500;700&display=swap" rel="stylesheet">
<style>
  :root {
    --brand-blue: #1468a8;
    --back-blue: #0f6aa8;
    --ink: #444444;
    --card-white: #f4f4f4;
    --backdrop: #2b2b2b;
    --white: #ffffff;
  }
  html, body {
    margin: 0;
    padding: 0;
    width: 1200px;
    height: 960px;
    overflow: hidden;
    background: var(--backdrop);
    font-family: "Roboto", Arial, sans-serif;
  }
  .canvas {
    position: relative;
    width: 1200px;
    height: 960px;
  }
  .card {
    position: absolute;
    left: 320px;
    width: 600px;
    box-shadow: 0 6px 14px rgba(0,0,0,0.45);
  }
  .card-back {
    top: 105px;
    height: 342px;
    background: var(--back-blue);
  }
  .card-front {
    top: 493px;
    height: 343px;
    background: var(--card-white);
    overflow: hidden;
  }
  .company-mark {
    position: absolute;
    left: 30px;
    top: 52px;
    display: flex;
    align-items: center;
    gap: 12px;
  }
  .company-mark .mark-square {
    width: 26px;
    height: 26px;
    background: var(--brand-blue);
  }
  .company-mark .company-name {
    font-weight: 700;
    font-size: 24px;
    letter-spacing: 0.5px;
    color: var(--brand-blue);
    line-height: 1;
  }
  .name-band {
    position: absolute;
    left: 0;
    top: 90px;
    width: 600px;
    height: 58px;
  }
  .manager {
    position: absolute;
    right: 27px;
    top: 94px;
    text-align: right;
    color: var(--white);
  }
  .manager-name {
    font-weight: 500;
    font-size: 22px;
    line-height: 26px;
  }
  .manager-title {
    font-size: 15px;
    line-height: 18px;
  }
  .property {
    position: absolute;
    left: 34px;
    top: 166px;
    color: var(--ink);
    font-size: 14.5px;
    line-height: 18px;
  }
  .building-name {
    color: var(--brand-blue);
    font-weight: 700;
    font-size: 15px;
  }
  .contact-list {
    list-style: none;
    margin: 8px 0 0;
    padding: 0;
  }
  .contact-list li {
    display: flex;
    align-items: center;
    gap: 8px;
    height: 19px;
  }
  .contact-list svg {
    width: 14px;
    height: 14px;
    fill: var(--brand-blue);
    flex: none;
  }
</style>
</head>
<body>
<div class="canvas">
  <div class="card card-back" aria-label="Card back"></div>

  <div class="card card-front">
    <div class="company-mark">
      <span class="mark-square"></span>
      <span class="company-name">HARBORVIEW ESTATES</span>
    </div>

    <svg class="name-band" viewBox="0 0 600 58" aria-hidden="true">
      <line x1="0" y1="57" x2="330" y2="57" stroke="#1468a8" stroke-width="1.5"/>
      <polygon points="360,0 600,0 600,57 323,57" fill="#1468a8"/>
    </svg>

    <div class="manager">
      <div class="manager-name">Marisol Delgado</div>
      <div class="manager-title">Resident Manager</div>
    </div>

    <div class="property">
      <div class="building-name">Bayside Court Apartments</div>
      <div>2145 Juniper Avenue</div>
      <div>Fairhaven, CA 95501</div>
      <ul class="contact-list">
        <li><svg viewBox="0 0 24 24"><path d="M6.6 10.8c1.4 2.8 3.8 5.1 6.6 6.6l2.2-2.2c.3-.3.7-.4 1-.2 1.1.4 2.3.6 3.6.6.6 0 1 .4 1 1V20c0 .6-.4 1-1 1C10.6 21 3 13.4 3 4c0-.6.4-1 1-1h3.5c.6 0 1 .4 1 1 0 1.3.2 2.5.6 3.6.1.3 0 .7-.2 1l-2.3 2.2z"/></svg>555-210-4480</li>
        <li><svg viewBox="0 0 24 24"><path d="M7 1h10a2 2 0 0 1 2 2v18a2 2 0 0 1-2 2H7a2 2 0 0 1-2-2V3a2 2 0 0 1 2-2zm0 3v14h10V4H7zm5 15.5a1 1 0 1 0 0 2 1 1 0 0 0 0-2z"/></svg>555-318-2764</li>
        <li><svg viewBox="0 0 24 24"><path d="M6 2h12v6H6zM3 9h18a1 1 0 0 1 1 1v8h-4v4H6v-4H2v-8a1 1 0 0 1 1-1zm5 7v4h8v-4H8z"/></svg>555-402-9135</li>
        <li><svg viewBox="0 0 24 24"><path d="M2 5h20v14H2V5zm2 2v.5l8 5 8-5V7H4zm0 2.8V17h16V9.8l-8 5-8-5z"/></svg>marisol@harborviewest.com</li>
        <li><svg viewBox="0 0 24 24"><path d="M12 2a10 10 0 1 0 0 20 10 10 0 0 0 0-20zm-1 17.9A8 8 0 0 1 4.1 10L9 15v1a2 2 0 0 0 2 2v1.9zm6.9-2.5A2 2 0 0 0 16 16h-1v-3a1 1 0 0 0-1-1H8v-2h2a1 1 0 0 0 1-1V7h2a2 2 0 0 0 2-2v-.4a8 8 0 0 1 2.9 12.8z"/></svg>www.harborviewest.com</li>
      </ul>
    </div>
  </div>
</div>
</body>
</html>
```